Business card for Sports Apparel business

DOUBLE SIDED DESIGN
We need business cards for a new sports apparel business. We are developing a protective headband for soccer initially.
Torvalle is focused on designing and developing head protection products to reduce the likelihood of concussion when playing sports. Exploring and understanding medical insights, material science research, current and former players experiences and governing bodies guidelines has allowed Torvalle to develop the safety, style, form and function requirements of a suitable product to bring to market.
Target Market(s)
Mums buying kits for the sons and daughters. Amateur footballers.
Industry/Entity Type
Sporting Good
Contact Information for Business Card
Martin Ashworth - CEO
Mobile: +44 7431589027
Email: martin@torvalle.co.uk
Tel: 0208 5519372
Helena Pargeter - COO
Mob: +44 7385 640117
Email: helena@torvalle.co.uk
Tel: 0208 5519372
Duncan Farrow - CCO
Mob: +44 7564 293081
Email: duncan@torvalle.co.uk
Tel: 0208 5519372
Look and feel
Each slider illustrates characteristics of the customer's brand and the style your logo design should communicate.

```html
<!DOCTYPE html>
<html lang="en">
<head>
<meta charset="utf-8">
<title>Torvalle business card</title>
<link href="https://fonts.googleapis.com/css2?family=Lato:wght@400;700;900&display=swap" rel="stylesheet">
<style>
  :root {
    --page: #d6d0c9;
    --card: #ecebe8;
    --brand-blue: #1b5e86;
    --name-blue: #1d5a80;
    --swoosh-grey: #5e5c5b;
    --logo-grey: #555759;
    --ink: #3a3a3a;
    --light-text: #eef3f6;
  }
  html, body {
    margin: 0;
    padding: 0;
    width: 1200px;
    height: 1047px;
    overflow: hidden;
    background: var(--page);
    font-family: "Lato", sans-serif;
  }
  .business-card {
    position: absolute;
    left: 80px;
    top: 242px;
    width: 1040px;
    height: 562px;
    border-radius: 24px;
    background: var(--card);
    overflow: hidden;
    box-shadow: 0 10px 30px rgba(0,0,0,0.12);
  }
  .card-waves {
    position: absolute;
    inset: 0;
    width: 1040px;
    height: 562px;
  }
  .person {
    position: absolute;
    right: 48px;
    top: 66px;
    text-align: right;
  }
  .person-name {
    margin: 0;
    font-weight: 900;
    font-size: 41px;
    line-height: 1;
    color: var(--name-blue);
    letter-spacing: 0.2px;
  }
  .person-role {
    margin: 6px 0 0;
    font-size: 22px;
    font-weight: 400;
    color: var(--ink);
  }
  .brand-name {
    position: absolute;
    left: 66px;
    top: 182px;
    margin: 0;
    font-weight: 700;
    font-size: 56px;
    letter-spacing: 3px;
    line-height: 1;
    color: var(--logo-grey);
  }
  .contact-list {
    position: absolute;
    right: 44px;
    top: 376px;
    margin: 0;
    padding: 0;
    list-style: none;
  }
  .contact-item {
    display: flex;
    justify-content: flex-end;
    align-items: center;
    height: 40px;
    font-size: 25px;
    color: var(--light-text);
    letter-spacing: 0.3px;
  }
  .contact-icon {
    width: 26px;
    height: 26px;
    margin-left: 22px;
    flex: none;
  }
</style>
</head>
<body>
  <main class="business-card">
    <svg class="card-waves" viewBox="0 0 1040 562" aria-hidden="true">
      <path d="M0 412 C120 440 220 500 330 488 C520 470 640 330 860 316 C950 311 1000 316 1040 322 L1040 562 L0 562 Z" fill="var(--brand-blue)"/>
      <path d="M0 356 C90 380 180 452 320 446 C500 438 700 322 880 312 C780 312 640 330 520 380 C420 420 330 442 250 436 C150 428 70 380 0 378 Z" fill="var(--swoosh-grey)"/>
    </svg>

    <div class="person">
      <h1 class="person-name">Martin Ashworth</h1>
      <p class="person-role">CEO</p>
    </div>

    <p class="brand-name">TORVALLE</p>

    <ul class="contact-list">
      <li class="contact-item">0208 5519372
        <svg class="contact-icon" viewBox="0 0 24 24"><path d="M3 9c0-3 4-5 9-5s9 2 9 5v2h-5V9c-2-1-6-1-8 0v2H3z" fill="var(--light-text)"/><rect x="6" y="12" width="12" height="8" rx="1.5" fill="var(--light-text)"/><circle cx="12" cy="16" r="2" fill="var(--brand-blue)"/></svg>
      </li>
      <li class="contact-item">+44 7431589027
        <svg class="contact-icon" viewBox="0 0 24 24"><rect x="6.5" y="2" width="11" height="20" rx="2" fill="none" stroke="var(--light-text)" stroke-width="2"/><circle cx="12" cy="18.5" r="1" fill="var(--light-text)"/></svg>
      </li>
      <li class="contact-item">martin@torvalle.co.uk
        <svg class="contact-icon" viewBox="0 0 24 24"><rect x="2" y="5" width="20" height="14" fill="var(--light-text)"/><path d="M2 5l10 8 10-8M2 19l7-7M22 19l-7-7" fill="none" stroke="var(--brand-blue)" stroke-width="1.5"/></svg>
      </li>
      <li class="contact-item">www.torvalle.co.uk
        <svg class="contact-icon" viewBox="0 0 24 24"><g fill="none" stroke="var(--light-text)" stroke-width="1.6"><circle cx="12" cy="12" r="9"/><ellipse cx="12" cy="12" rx="4" ry="9"/><path d="M3 12h18M5 7h14M5 17h14"/></g></svg>
      </li>
    </ul>
  </main>
</body>
</html>
```